Website design for legal tech start up in Switzerland (B2B)

We are for a legal tech start up in Switzerland called KOVA. We have been running since August 2016. This will be our first live website.

We need a website designed and business card design for our start-up in Switzerland. We also need the Web design to be converted into HTML and CSS files.

Function of website:
• To inform potential customers of our services
• Form a key part of our digital marketing and sales footprint.
• Branding

Please find attached logo.
Updates

Project Deadline Extended Reason: Giving us time to review submissions and provide opportunity for more submissions. Added Thursday, February 16, 2017

Project Deadline Extended
Reason: Looking for more idea's not necessarily set on blue and grey colours only.

Target Market(s)

B2B tech powered legal services.

Industry/Entity Type

Legal

Contact Information for Business Card

Lean and slick design.

Coding

Coded - Design and coding required

Number of Pages Required

5+ page

Requirements
Must have
• VERY LEAN AND CLEAN DESIGN!
• We have received many great standard designs, but we are looking for something more out-of-the box: You can get inspiration from these designs: http://www.pixelvane.com/websites/clean/
• Thanks!!
• Easy content management system
• Well structured coding for additional development
• Responsive webpage for all types of devices
• SEO optimized
• Tabs (Home, services, team, careers, blog, contact us)
• Colour scheme complementary to logo
Nice to have
• Look and Design - Approachable, High-tech, Modern
• Easy to add chat bot capability in future
Should not have
• Too busy/ too much clutter
• Not take to long to load

```html
<!DOCTYPE html>
<html lang="en">
<head>
<meta charset="utf-8">
<title>KOVA – Legal Tech</title>
<link href="https://fonts.googleapis.com/css2?family=Montserrat:wght@400;500;600;700&family=Open+Sans:wght@400;600&family=Roboto+Condensed:wght@700&display=swap" rel="stylesheet">
<style>
:root{
  --ink:#333;
  --text:#555;
  --muted:#8a8a8a;
  --navy:#1c3a6b;
  --charcoal:#454545;
  --card-text:#b9b9b9;
  --white:#fff;
  --line:#e2e2e2;
  --footer-bar:#ececec;
}
*{box-sizing:border-box;margin:0;padding:0}
html,body{width:1200px;height:2459px;overflow:hidden;background:var(--white)}
body{font-family:"Open Sans",Arial,sans-serif;color:var(--text);position:relative}
.abs{position:absolute}
.center{left:0;width:1200px;text-align:center}

/* header */
.site-header{top:0;left:0;width:1200px;height:88px;background:var(--white)}
.brand{left:98px;top:14px;font-family:"Montserrat",sans-serif;font-weight:700;font-size:50px;letter-spacing:2px;color:#3c3c3c;line-height:60px}
.main-nav{right:98px;top:31px;display:flex;gap:6px;font-family:"Montserrat",sans-serif;font-size:14px;color:var(--ink)}
.main-nav a{padding:6px 14px;color:var(--ink);text-decoration:none;border:1px solid transparent}
.main-nav a.active{border-color:#9a9a9a;color:var(--navy)}

/* hero */
.hero{top:88px;left:0;width:1200px;height:584px;background:linear-gradient(180deg,#3d4c7e 0%,#7a5a86 28%,#c27a6a 45%,#6b6a78 62%,#2c3344 100%)}
.hero-kicker{top:272px;font-family:"Montserrat",sans-serif;font-size:20px;color:var(--white);letter-spacing:1px}
.hero-title{top:292px;font-family:"Montserrat",sans-serif;font-size:54px;font-weight:500;color:var(--white);letter-spacing:2px}
.hero-lead{top:352px;left:400px;width:400px;text-align:center;font-family:"Montserrat",sans-serif;font-weight:600;font-size:14px;line-height:26px;color:var(--white)}
.hero-btn{top:420px;left:530px;width:140px;height:38px;border:2px solid var(--white);color:var(--white);font-family:"Montserrat",sans-serif;font-size:21px;line-height:34px;text-align:center}
.round-arrow{width:32px;height:32px;border-radius:50%;background:var(--white);border:1px solid #ccc;display:flex;align-items:center;justify-content:center}

/* intro */
.section-title{font-family:"Montserrat",sans-serif;font-size:29px;color:var(--ink);font-weight:500}
.intro-text{top:766px;left:180px;width:840px;text-align:center;font-size:12.5px;line-height:22px;color:var(--text)}

/* services */
.service{top:968px;width:266px;height:332px;text-align:center;color:var(--white)}
.service.is-featured{background:var(--navy)}
.service.is-plain{background:var(--charcoal)}
.service svg.icon{margin-top:34px}
.service h3{font-family:"Montserrat",sans-serif;font-weight:400;font-size:19px;margin-top:16px}
.service p{font-size:12px;line-height:21px;color:var(--card-text);margin:14px 26px 0}
.service .round-arrow{margin:16px auto 0;width:34px;height:34px;border:none}
.service.is-featured p{color:#9fb0cc}

/* team */
.team{top:1360px;left:0;width:1200px;height:567px;background:linear-gradient(180deg,#1f3566 0%,#3b4f86 30%,#5d6f9c 60%,#33477a 100%)}
.team-title{top:1390px;font-family:"Montserrat",sans-serif;font-size:26px;font-weight:500;color:var(--white)}
.team-sub{top:1428px;font-size:12px;color:#dfe5f2}
.member{top:1471px;width:216px}
.member .photo{width:216px;height:177px;background:linear-gradient(180deg,#ededed,#cfcfcf)}
.member .dots{height:22px;text-align:center;color:var(--white);font-size:14px;line-height:16px;letter-spacing:2px}
.member .card{background:var(--white);height:175px;text-align:center;padding-top:20px}
.member h4{font-family:"Roboto Condensed",sans-serif;font-size:14px;color:#222}
.member p{font-size:11.5px;line-height:20px;color:var(--text);margin:16px 22px 0}
.socials{display:flex;justify-content:center;gap:7px;margin-top:10px}
.socials span{width:24px;height:24px;border-radius:50%;border:1px solid #555}
.socials.is-filled span{background:#555}
.pager{top:1884px;left:577px;display:flex;gap:6px}
.pager span{width:6px;height:6px;border-radius:50%;border:1px solid var(--white)}

/* call to action */
.cta{top:1927px;left:0;width:1200px;height:100px;background:var(--charcoal)}
.cta-text{top:1960px;left:195px;width:580px;white-space:nowrap;font-family:"Montserrat",sans-serif;font-weight:500;font-size:20px;letter-spacing:2px;color:var(--white)}
.cta-btn{top:1951px;left:811px;width:171px;height:46px;background:var(--white);font-family:"Montserrat",sans-serif;font-weight:600;font-size:15px;color:#222;text-align:center;line-height:46px;box-shadow:0 2px 3px rgba(0,0,0,.3)}
.cta-notch{top:2027px;left:587px}

/* footer */
.footer-col{top:2066px;width:235px}
.footer-col h5{font-family:"Montserrat",sans-serif;font-weight:400;font-size:15px;letter-spacing:1px;color:#444;margin-bottom:20px}
.about p{font-size:10.5px;line-height:20px;color:var(--text)}
.contact-item{display:flex;gap:14px;margin-top:18px;font-size:11px;line-height:17px;color:var(--text)}
.contact-item svg{flex:none;margin-top:3px}
.post{display:flex;gap:18px;padding-bottom:12px;margin-bottom:14px;border-bottom:1px solid var(--line);width:230px}
.post .thumb{width:52px;height:40px;flex:none;background:linear-gradient(135deg,#dfe3ea,#8d96a6)}
.post h6{font-weight:400;font-size:13px;line-height:20px;color:#444}
.post time{font-size:10px;color:var(--text)}
.service-links li{list-style:none;font-size:11px;color:var(--text);padding:4px 0 12px 12px;border-bottom:1px dashed #aaa;margin-bottom:6px;width:186px;position:relative}
.service-links li::before{content:"›";position:absolute;left:0;top:2px}
.newsletter{display:flex;margin-top:4px}
.newsletter .field{width:200px;height:34px;border:1px solid #ddd;font-size:11px;line-height:32px;padding-left:14px;color:#555}
.newsletter .go{width:32px;height:34px;background:#333;display:flex;align-items:center;justify-content:center}
.footer-brand{font-family:"Montserrat",sans-serif;font-weight:700;font-size:46px;letter-spacing:2px;color:#3c3c3c;margin-top:16px;line-height:56px}
.footer-social{display:flex;gap:14px;align-items:center;margin-top:18px;padding-left:6px;color:#333}
.footer-social span{width:14px;height:14px;border-radius:50%;background:#333}

.bottom-bar{top:2418px;left:0;width:1200px;height:41px;background:var(--footer-bar);font-size:11px;color:#333;line-height:41px}
.bottom-nav{left:116px}
.copyright{right:60px}
</style>
</head>
<body>

<header class="site-header abs">
  <div class="brand abs">KOVA</div>
  <nav class="main-nav abs">
    <a class="active">Home</a><a>Services</a><a>Team</a><a>Careers</a><a>Blog</a><a>Contact Us</a>
  </nav>
</header>

<section class="hero abs" role="img" aria-label="Evening view of an old town with a church spire and a stone bridge over a river"></section>
<div class="hero-kicker abs center">WELCOME</div>
<div class="hero-title abs center">KOVA</div>
<p class="hero-lead abs">Neque porro quisquam est qui dolorem ipsum quia dolor sit amet, consectetur, adipisci velit...</p>
<div class="hero-btn abs">Click here</div>
<div class="round-arrow abs" style="top:656px;left:584px">
  <svg width="12" height="8" viewBox="0 0 12 8"><path d="M1 1l5 5 5-5" fill="none" stroke="#555" stroke-width="1.5"/></svg>
</div>

<h2 class="section-title abs center" style="top:712px">Welcome To Kova</h2>
<p class="intro-text abs">Denouncing pleasure and praising pain was born and I will give you a complete account of the system, and expound the actual teachings of the great explorer of the truth, the master-builder of human happiness. No one rejects, dislikes, or avoids pleasure itself, because it is pleasure</p>
<div class="round-arrow abs" style="top:830px;left:584px">
  <svg width="12" height="8" viewBox="0 0 12 8"><path d="M1 1l5 5 5-5" fill="none" stroke="#555" stroke-width="1.5"/></svg>
</div>

<h2 class="section-title abs center" style="top:884px">Our Services</h2>

<article class="service is-featured abs" style="left:170px">
  <svg class="icon" width="64" height="60" viewBox="0 0 64 60" fill="none" stroke="#fff" stroke-width="2">
    <path d="M4 18L32 4l28 14z"/><rect x="6" y="18" width="52" height="5"/>
    <path d="M13 23v26M21 23v26M29 23v26M37 23v26M45 23v26M53 23v26"/>
    <rect x="6" y="49" width="52" height="4"/><rect x="2" y="53" width="60" height="4"/>
  </svg>
  <h3>Estate Planning</h3>
  <p>Nam libero tempore, cum soluta nobis est eligendi optio cumque nihil impedit quo minus id quod maxime placeat facere possimus, omnis voluptas assumenda est</p>
  <div class="round-arrow"><svg width="8" height="12" viewBox="0 0 8 12"><path d="M1 1l5 5-5 5" fill="none" stroke="#333" stroke-width="1.5"/></svg></div>
</article>

<article class="service is-plain abs" style="left:468px">
  <svg class="icon" width="104" height="60" viewBox="0 0 104 60" fill="none" stroke="#fff" stroke-width="2">
    <circle cx="30" cy="20" r="10"/><path d="M12 56c0-14 8-22 18-22s18 8 18 22z"/>
    <circle cx="74" cy="20" r="10"/><path d="M56 56c0-14 8-22 18-22s18 8 18 22z"/>
    <circle cx="52" cy="16" r="11"/><path d="M32 56c0-16 9-25 20-25s20 9 20 25z"/>
  </svg>
  <h3>Employment Law</h3>
  <p>Nam libero tempore, cum soluta nobis est eligendi optio cumque nihil impedit quo minus id quod maxime placeat facere possimus, omnis voluptas assumenda est</p>
  <div class="round-arrow"><svg width="8" height="12" viewBox="0 0 8 12"><path d="M1 1l5 5-5 5" fill="none" stroke="#333" stroke-width="1.5"/></svg></div>
</article>

<article class="service is-plain abs" style="left:765px">
  <svg class="icon" width="76" height="60" viewBox="0 0 76 60" fill="none" stroke="#fff" stroke-width="2">
    <circle cx="22" cy="14" r="9"/><path d="M6 58V38c0-8 7-12 16-12s16 4 16 12v20"/>
    <circle cx="54" cy="14" r="9"/><path d="M38 58V38c0-8 7-12 16-12s16 4 16 12v20"/>
    <circle cx="38" cy="38" r="6"/><path d="M28 58c0-8 4-12 10-12s10 4 10 12"/>
  </svg>
  <h3>Family Law</h3>
  <p>Nam libero tempore, cum soluta nobis est eligendi optio cumque nihil impedit quo minus id quod maxime placeat facere possimus, omnis voluptas assumenda est</p>
  <div class="round-arrow"><svg width="8" height="12" viewBox="0 0 8 12"><path d="M1 1l5 5-5 5" fill="none" stroke="#333" stroke-width="1.5"/></svg></div>
</article>

<section class="team abs" role="img" aria-label="Snowy mountain range under a blue dusk sky"></section>
<h2 class="team-title abs center">Team</h2>
<p class="team-sub abs center">Neque porro quisquam est qui dolorem ipsum quia dolor sit amet,</p>

<article class="member abs" style="left:128px">
  <div class="photo" role="img" aria-label="Portrait of Theo Varga"></div>
  <div class="dots">•••</div>
  <div class="card"><h4>THEO VARGA</h4><p>Duis quis odio molestie, eleifend lacus feugiat, convallis lorem. Cum sociis natoque penatibus et.</p>
    <div class="socials"><span></span><span></span><span></span><span></span></div></div>
</article>
<article class="member abs" style="left:371px">
  <div class="photo" role="img" aria-label="Portrait of Noah Brandt"></div>
  <div class="dots">•••</div>
  <div class="card"><h4>NOAH BRANDT</h4><p>Duis quis odio molestie, eleifend lacus feugiat, convallis lorem. Cum sociis natoque penatibus et.</p>
    <div class="socials"><span></span><span></span><span></span><span></span></div></div>
</article>
<article class="member abs" style="left:613px">
  <div class="photo" role="img" aria-label="Portrait of Felix Amsler"></div>
  <div class="dots">•••</div>
  <div class="card"><h4>FELIX AMSLER</h4><p>Duis quis odio molestie, eleifend lacus feugiat, convallis lorem. Cum sociis natoque penatibus et.</p>
    <div class="socials is-filled"><span></span><span></span><span></span><span></span></div></div>
</article>
<article class="member abs" style="left:856px">
  <div class="photo" role="img" aria-label="Portrait of Luca Steiner"></div>
  <div class="dots">•••</div>
  <div class="card"><h4>LUCA STEINER</h4><p>Duis quis odio molestie, eleifend lacus feugiat, convallis lorem. Cum sociis natoque penatibus et.</p>
    <div class="socials"><span></span><span></span><span></span><span></span></div></div>
</article>
<div class="pager abs"><span></span><span></span><span></span><span></span></div>

<section class="cta abs"></section>
<div class="cta-text abs">NEQUE PORRO QUISQUAM EST QUI DOLOREM</div>
<div class="cta-btn abs">Contact Us</div>
<svg class="cta-notch abs" width="26" height="13" viewBox="0 0 26 13"><path d="M0 0h26L13 13z" fill="#454545"/></svg>

<div class="footer-col about abs" style="left:98px">
  <h5>ABOUT US</h5>
  <p>Lorem ipsum dolor sit amet consec tetur adipiscing elit nulla aliquet pretium nisi in cursus maecenas nec eleifen.</p>
  <div class="contact-item">
    <svg width="10" height="10" viewBox="0 0 10 10"><path d="M10 0L0 4l4 2 2 4z" fill="#444"/></svg>
    <div>Location<br>123 suscipit ipsum nam auctor mauris dui, ac sollicitudin mauris, Zurich</div>
  </div>
  <div class="contact-item">
    <svg width="10" height="10" viewBox="0 0 10 10"><path d="M2 0l2 3-1 1c1 2 2 3 3 3l1-1 3 2-1 2C4 10 0 6 0 2z" fill="#444"/></svg>
    <div>Phone :<br>+41 44 555 0192</div>
  </div>
  <div class="contact-item">
    <svg width="11" height="9" viewBox="0 0 11 9"><rect x=".5" y=".5" width="10" height="8" fill="none" stroke="#444"/><path d="M.5.5l5 4 5-4" fill="none" stroke="#444"/></svg>
    <div>Email Address :<br>hello@kova-legal.ch</div>
  </div>
</div>

<div class="footer-col abs" style="left:355px">
  <h5>LATEST BLOG</h5>
  <div class="post"><div class="thumb" role="img" aria-label="Business meeting photo"></div><div><h6>Lorem ipsum dolor sit amet, consectetur</h6><time>21th July 2015</time></div></div>
  <div class="post"><div class="thumb" role="img" aria-label="Office worker photo"></div><div><h6>Lorem ipsum dolor sit amet, consectetur</h6><time>21th July 2015</time></div></div>
  <div class="post"><div class="thumb" role="img" aria-label="Colleagues at work photo"></div><div><h6>Lorem ipsum dolor sit amet, consectetur</h6><time>21th July 2015</time></div></div>
</div>

<div class="footer-col abs" style="left:612px">
  <h5>OUR SERVICES</h5>
  <ul class="service-links">
    <li>Estate Planning</li><li>Employment Law</li><li>Family Law</li><li>Services</li><li>Support</li><li>Forums</li>
  </ul>
</div>

<div class="footer-col abs" style="left:869px">
  <h5>NEWSLETTER</h5>
  <div class="newsletter"><div class="field">Enter you Email</div>
    <div class="go"><svg width="10" height="10" viewBox="0 0 10 10"><path d="M0 4h6V1l4 4-4 4V6H0z" fill="#fff"/></svg></div></div>
  <div class="footer-brand">KOVA</div>
  <div class="footer-social">-<span></span><span></span><span></span><span></span><span></span><span></span>-</div>
</div>

<footer class="bottom-bar abs">
  <div class="bottom-nav abs">Home &nbsp;-&nbsp; Services &nbsp;-&nbsp; Team &nbsp;-&nbsp; Careers &nbsp;-&nbsp; Blog &nbsp;-&nbsp; Contact Us</div>
  <div class="copyright abs">Copyrights © 2017 - All Rights Reserved &nbsp;&nbsp;&nbsp;&nbsp; M1</div>
</footer>

</body>
</html>
```